Health Supplement Series for 60 tablets of pure Amber Vine Core powder

We need a packaging design theme for a health supplement for international consumers. Our initial product is called 'Amber Vine Core'. It is for general health and is particularly effective for diabetic symptoms.
We would like to see designs that are clean and fresh.
It should give the impression of professional, premium pharmaceutical grade products.
Our company logo is attached below.

Target Market(s)

International

Industry/Entity Type

Health And Wellness

Font styles to use
Serif
Sans Serif

Requirements
Must have
• Bottle and box packaging required.
• 1st product is bottle of 60 tablets of 0.5gm each.
Should not have
• Seals and other "must buy" "guaranteed" etc

```html
<!DOCTYPE html>
<html lang="en">
<head>
<meta charset="utf-8">
<title>Amber Vine Core — Label</title>
<link rel="stylesheet" href="https://fonts.googleapis.com/css2?family=Open+Sans:wght@400;700&display=swap">
<style>
  :root {
    --page-bg: #efefef;
    --label-white: #ffffff;
    --green-main: #7cb82f;
    --green-deep: #5c9a1c;
    --green-light: #9ccf55;
    --green-pale: #e4f1d2;
    --ink-grey: #555555;
  }
  html, body {
    margin: 0;
    padding: 0;
    overflow: hidden;
  }
  body {
    width: 1158px;
    height: 1200px;
    background: var(--page-bg);
    font-family: "Open Sans", Arial, sans-serif;
  }
  .label {
    position: absolute;
    left: 132px;
    top: 48px;
    width: 893px;
    height: 1103px;
    background: var(--label-white);
    overflow: hidden;
    box-shadow: 0 4px 18px rgba(0,0,0,0.08);
  }
  .label__waves {
    position: absolute;
    inset: 0;
    width: 100%;
    height: 100%;
  }
  .product-mark {
    position: absolute;
    left: 400px;
    top: 189px;
    width: 273px;
    height: 598px;
    border-radius: 140px 140px 140px 40px;
    background: radial-gradient(circle at 60% 30%, var(--green-pale), rgba(228,241,210,0.25) 70%);
  }
  .product-name {
    position: absolute;
    left: 120px;
    top: 438px;
    width: 460px;
    margin: 0;
    text-align: center;
    color: var(--green-main);
    font-weight: 700;
    font-size: 96px;
    line-height: 101px;
    letter-spacing: 1px;
    text-transform: uppercase;
  }
  .product-copy {
    position: absolute;
    left: 190px;
    top: 840px;
    width: 460px;
    margin: 0;
    text-align: center;
    color: var(--ink-grey);
    font-size: 18px;
    line-height: 26px;
  }
  .maker {
    position: absolute;
    left: 270px;
    top: 940px;
    display: flex;
    align-items: center;
    gap: 12px;
    color: var(--green-deep);
    font-weight: 700;
  }
  .maker__square {
    width: 56px;
    height: 76px;
    background: var(--green-main);
  }
  .maker__name {
    font-size: 44px;
    line-height: 46px;
    letter-spacing: 2px;
  }
  .maker__name span {
    display: block;
    font-size: 22px;
    line-height: 26px;
    letter-spacing: 0.5px;
  }
  .side-copy {
    position: absolute;
    left: 826px;
    top: 304px;
    width: 588px;
    margin: 0;
    transform-origin: left top;
    transform: rotate(-90deg) translateX(-588px);
    color: var(--ink-grey);
    font-size: 16px;
    line-height: 22px;
  }
</style>
</head>
<body>
  <main class="label">
    <svg class="label__waves" viewBox="0 0 893 1103" aria-hidden="true">
      <path d="M0 0 H893 V53 C700 80 420 130 0 74 Z" fill="var(--green-main)"/>
      <path d="M0 74 C420 130 700 80 893 53 V66 C700 95 420 140 0 86 Z" fill="var(--green-light)" opacity="0.6"/>
      <path d="M0 945 C40 1010 120 1050 260 1055 C480 1060 700 1030 893 1000 V1103 H0 Z" fill="var(--green-light)"/>
      <path d="M0 985 C60 1040 160 1068 300 1070 C520 1072 720 1050 893 1030 V1103 H0 Z" fill="var(--green-main)"/>
    </svg>

    <div class="product-mark" role="img" aria-label="Product emblem: a green leaf-like figure with a round head arcing upward"></div>

    <h1 class="product-name">Amber<br>Vine<br>Core</h1>

    <p class="product-copy">Lorem ipsum dolor sit amet, consectetur adipisc-<br>ing elit. Ut mollis lobortis tempus. Donec lobortis</p>

    <div class="maker">
      <div class="maker__square"></div>
      <div class="maker__name">NORVALE<span>BIOTECH LIMITED</span></div>
    </div>

    <p class="side-copy">Lorem ipsum dolor sit amet, consectetur adipiscing elit. Ut mollis lo-<br>bortis tempus. Donec lobortis vitae lacus et accumsan. Donec in</p>
  </main>
</body>
</html>
```